Diverse, up-scale salon needs eye-catching, unique business cards.

We are looking for a unique business card design for our stylist but that can also be multi functional and used for appointment reminder and referrals. I will need a design in a format that I can modify names and titles going forward. In the past we have had a dark background with the logo on one side, and stylist and contact information on the other but we are open to all ideas. I have included our mission statement as well as branded colors below. The statement doesn't need to go on the card, it's just a reference for target market. We need space for the stylists name, title, instagram handle and then the salons phone number, website and address. I am also open to adding a spot for a qr code linked to the stylist instagram or the salon booking link.

primary brand colors:
#333333 #233415 #36502a #93874a #000000
Mission statement:
Vessolin Hair Studio, a high-end salon located in the lively Downtown Farmington, Michigan, is committed to providing exceptional services in a welcoming and relaxed environment to meet the needs of our diverse clientele.
Our salon specializes in contemporary custom haircuts, coloring, extensions, and barbering and beard grooming services. Our team of skilled stylists is passionate and inventive in their hair styling techniques. At the heart of our salon are values centered on quality, innovation, creativity, and above all, comfort. These core values are evident in every appointment across our customizable array of services.
Our goal is to establish a benchmark for exceptional hair care for every human.
Website: www.vessolinhairstudio.example
instagram: @vessolinhairstudio
address: 41782 Pelham Crest Rd, Farmington MI
phone: 248-613-4087

Industry/Entity Type

Hair Salon

Contact Information for Business Card

Stylist name, title, phone, instagram, website, address, (optional qr code)

Requirements
Should not have
• Does not need mission statement on the card.

```html
<!DOCTYPE html>
<html lang="en">
<head>
<meta charset="utf-8">
<title>Vessolin Hair Studio – Business Card</title>
<link rel="stylesheet" href="https://fonts.googleapis.com/css2?family=Open+Sans:wght@400;700&display=swap">
<style>
  :root {
    --backdrop: #e9e4dc;
    --panel-dark: #1e1e1e;
    --panel-dark-edge: #383838;
    --panel-light: #ebe3d6;
    --gold: #98823f;
    --text-light: #cfcac2;
  }
  * { margin: 0; padding: 0; box-sizing: border-box; }
  html, body {
    width: 1200px;
    height: 1047px;
    overflow: hidden;
    background: var(--backdrop);
    font-family: "Open Sans", sans-serif;
  }
  .card {
    position: absolute;
    left: 80px;
    top: 240px;
    width: 1040px;
    height: 568px;
    border-radius: 24px;
    overflow: hidden;
    box-shadow: 0 14px 40px rgba(0,0,0,0.18);
  }
  .card-shape { position: absolute; inset: 0; }
  .stylist-name {
    position: absolute; left: 54px; top: 30px;
    font-size: 33px; font-weight: 700; letter-spacing: 0.5px;
    color: var(--gold);
  }
  .stylist-title {
    position: absolute; left: 56px; top: 78px;
    font-size: 24px; color: var(--text-light);
  }
  .salon-address {
    position: absolute; left: 52px; top: 218px;
    font-size: 23px; line-height: 35px; color: var(--text-light);
  }
  .contact-list {
    position: absolute; left: 50px; top: 384px;
    list-style: none;
    font-size: 23px; line-height: 35.5px; color: var(--text-light);
  }
  .contact-list li { display: flex; align-items: center; gap: 8px; }
  .contact-icon { width: 20px; height: 20px; flex: none; }
  .brand-mark {
    position: absolute; left: 484px; top: 0; width: 556px; height: 568px;
    display: flex; align-items: center; justify-content: center;
  }
  .brand-name {
    font-size: 38px; font-weight: 700; line-height: 50px;
    color: var(--gold); text-align: center; text-transform: uppercase;
    letter-spacing: 2px;
  }
</style>
</head>
<body>
  <div class="card">
    <svg class="card-shape" width="1040" height="568" viewBox="0 0 1040 568">
      <defs>
        <linearGradient id="darkPanel" x1="0" y1="0" x2="1" y2="0">
          <stop offset="0" stop-color="var(--panel-dark)"/>
          <stop offset="1" stop-color="var(--panel-dark-edge)"/>
        </linearGradient>
      </defs>
      <rect width="1040" height="568" fill="url(#darkPanel)"/>
      <rect x="600" width="440" height="568" fill="var(--panel-light)"/>
      <circle cx="761" cy="284" r="329" fill="var(--panel-light)"/>
      <circle cx="761" cy="284" r="238" fill="none" stroke="var(--gold)" stroke-width="6"/>
    </svg>

    <h1 class="stylist-name">DARIAN HOLT</h1>
    <p class="stylist-title">Managing Director</p>

    <p class="salon-address">41782 Pelham Crest Rd,<br>Farmington MI</p>

    <ul class="contact-list">
      <li>
        <svg class="contact-icon" viewBox="0 0 20 20"><path d="M5 2l3 4-2 2c1 2 3 4 5 5l2-2 4 3-2 3C8 17 3 12 2 5z" fill="var(--text-light)"/></svg>
        248-613-4087
      </li>
      <li>
        <svg class="contact-icon" viewBox="0 0 20 20"><rect x="2" y="5" width="16" height="11" rx="1.5" fill="none" stroke="var(--text-light)" stroke-width="2"/><path d="M2 6l8 6 8-6" fill="none" stroke="var(--text-light)" stroke-width="2"/></svg>
        info@vessolinhairstudio.example
      </li>
      <li>
        <svg class="contact-icon" viewBox="0 0 20 20"><circle cx="10" cy="10" r="6" fill="none" stroke="var(--text-light)" stroke-width="2"/></svg>
        @vessolinhairstudio
      </li>
      <li>
        <svg class="contact-icon" viewBox="0 0 20 20"><circle cx="10" cy="10" r="7" fill="none" stroke="var(--text-light)" stroke-width="2"/><path d="M3 10h14M10 3c3 3 3 11 0 14M10 3c-3 3-3 11 0 14" fill="none" stroke="var(--text-light)" stroke-width="1.5"/></svg>
        www.vessolinhairstudio.example
      </li>
    </ul>

    <div class="brand-mark">
      <p class="brand-name">Vessolin<br>Hair Studio</p>
    </div>
  </div>
</body>
</html>
```